Law Enforcement Services Leader Seeking Graphic Design for 2 Roll Up Banners

Vantrell Roster Group( the leader in police administrative services) needs a graphic designer to develop two separate graphics for a pair of 33" edge retractable roll-up banners to complete our trade show booth display. Please reference our website at www.vantrellrostergroup.com as well as the uploaded files to get a feel for our branding.

```html
<!DOCTYPE html>
<html lang="en">
<head>
<meta charset="utf-8">
<title>Vantrell Roster Group – Roll-up Banners</title>
<link rel="stylesheet" href="https://fonts.googleapis.com/css2?family=Montserrat:wght@400;500;600&display=swap">
<style>
  :root {
    --page-bg: #c9c9c9;
    --navy-deep: #03163a;
    --navy: #0a2f66;
    --navy-mid: #0d4a8f;
    --cyan: #14b4ee;
    --cyan-soft: #29c4f5;
    --white: #ffffff;
    --divider: rgba(255,255,255,0.22);
  }
  * { box-sizing: border-box; margin: 0; padding: 0; }
  html, body { width: 728px; height: 1200px; overflow: hidden; }
  body {
    background: linear-gradient(135deg, #dcdcdc 0%, var(--page-bg) 60%, #b3b3b3 100%);
    font-family: "Montserrat", sans-serif;
    position: relative;
  }
  .banner {
    position: absolute;
    top: 203px;
    width: 336px;
    height: 793px;
    overflow: hidden;
    color: var(--white);
    box-shadow: 0 6px 18px rgba(0,0,0,0.18);
  }
  .banner--team { left: 16px; }
  .banner--ops { left: 376px; }
  .banner__art {
    position: absolute;
    inset: 0;
    width: 100%;
    height: 100%;
    display: block;
  }
  .brand {
    position: absolute;
    top: 50px;
    left: 0;
    width: 100%;
    text-align: center;
    font-weight: 500;
    color: var(--white);
    text-transform: uppercase;
  }
  .brand__line {
    display: block;
    font-size: 21px;
    letter-spacing: 2.5px;
    line-height: 1.15;
  }
  .brand__line--sub {
    font-size: 16px;
    letter-spacing: 7px;
  }
  .feature {
    position: absolute;
    left: 101px;
    width: 204px;
    font-size: 11.3px;
    line-height: 15.5px;
    font-weight: 500;
  }
  .feature-icon {
    position: absolute;
    left: 35px;
    width: 48px;
    height: 52px;
  }
  .divider {
    position: absolute;
    left: 34px;
    width: 262px;
    height: 1px;
    background: var(--divider);
  }
  .site-url {
    position: absolute;
    top: 746px;
    left: 0;
    width: 100%;
    text-align: center;
    font-size: 15px;
    font-weight: 400;
    letter-spacing: 0.2px;
  }
  .site-url strong { font-weight: 600; }
</style>
</head>
<body>

<!-- Banner 1: Team -->
<section class="banner banner--team">
  <svg class="banner__art" viewBox="0 0 500 1180" preserveAspectRatio="none" aria-hidden="true">
    <defs>
      <linearGradient id="teamBg" x1="0" y1="0" x2="0" y2="1">
        <stop offset="0" stop-color="#03163a"/>
        <stop offset="0.45" stop-color="#0a2f66"/>
        <stop offset="1" stop-color="#0d4a8f"/>
      </linearGradient>
      <linearGradient id="teamPhoto" x1="0" y1="0" x2="1" y2="1">
        <stop offset="0" stop-color="#8b2fc9"/>
        <stop offset="0.45" stop-color="#5a1f8a"/>
        <stop offset="1" stop-color="#1a0e3a"/>
      </linearGradient>
      <linearGradient id="teamBase" x1="0" y1="0" x2="1" y2="1">
        <stop offset="0" stop-color="#14b4ee"/>
        <stop offset="1" stop-color="#0b5fae"/>
      </linearGradient>
    </defs>
    <rect width="500" height="1180" fill="url(#teamBg)"/>
    <polygon points="0,168 165,222 0,268" fill="#29c4f5"/>
    <polygon points="500,478 500,580 330,530" fill="#14b4ee"/>
    <polygon points="1020,0" fill="none"/>
    <polygon points="0,1020 500,1060 500,1180 0,1180" fill="url(#teamBase)"/>
    <polygon points="270,1035 500,1060 500,1110" fill="#0a2f66"/>
  </svg>
  <svg class="banner__art" viewBox="0 0 500 1180" preserveAspectRatio="none" role="img" aria-label="Photo: two police officers standing arms crossed beside a patrol car with purple emergency light glow">
    <polygon points="0,268 165,222 500,168 500,478 330,530 0,580" fill="url(#teamPhoto)"/>
  </svg>

  <div class="brand">
    <span class="brand__line">Vantrell Roster</span>
    <span class="brand__line brand__line--sub">Group</span>
  </div>

  <svg class="feature-icon" style="top:409px" viewBox="0 0 48 52" aria-hidden="true">
    <polygon points="24,2 45,14 45,38 24,50 3,38 3,14" fill="#fff" stroke="#14b4ee" stroke-width="3"/>
    <rect x="17" y="14" width="14" height="24" rx="2" fill="none" stroke="#0a2f66" stroke-width="1.6"/>
    <circle cx="24" cy="24" r="3" fill="none" stroke="#0a2f66" stroke-width="1.4"/>
    <line x1="21" y1="34" x2="27" y2="34" stroke="#0a2f66" stroke-width="1.4"/>
  </svg>
  <p class="feature" style="top:412px">We're more than an app. We're a fully-staffed service provider leveraging state-of-the-art technology.</p>
  <div class="divider" style="top:476px"></div>

  <svg class="feature-icon" style="top:487px" viewBox="0 0 48 52" aria-hidden="true">
    <polygon points="24,2 45,14 45,38 24,50 3,38 3,14" fill="#fff" stroke="#14b4ee" stroke-width="3"/>
    <circle cx="16" cy="24" r="3" fill="none" stroke="#0a2f66" stroke-width="1.4"/>
    <circle cx="24" cy="24" r="3" fill="none" stroke="#0a2f66" stroke-width="1.4"/>
    <circle cx="32" cy="24" r="3" fill="none" stroke="#0a2f66" stroke-width="1.4"/>
    <path d="M11 35 q5-7 10 0 M19 35 q5-7 10 0 M27 35 q5-7 10 0" fill="none" stroke="#0a2f66" stroke-width="1.4"/>
  </svg>
  <p class="feature" style="top:496px">There's no conflict of interest. We work directly for your agency, not your vendors.</p>
  <div class="divider" style="top:550px"></div>

  <svg class="feature-icon" style="top:561px" viewBox="0 0 48 52" aria-hidden="true">
    <polygon points="24,2 45,14 45,38 24,50 3,38 3,14" fill="#fff" stroke="#14b4ee" stroke-width="3"/>
    <rect x="13" y="16" width="22" height="15" rx="1.5" fill="none" stroke="#0a2f66" stroke-width="1.6"/>
    <line x1="24" y1="31" x2="24" y2="36" stroke="#0a2f66" stroke-width="1.6"/>
    <line x1="18" y1="36" x2="30" y2="36" stroke="#0a2f66" stroke-width="1.6"/>
    <circle cx="28" cy="22" r="3" fill="none" stroke="#0a2f66" stroke-width="1.4"/>
  </svg>
  <p class="feature" style="top:570px">We provide on-duty software as well as API integration into other on-duty software packages</p>
  <div class="divider" style="top:620px"></div>

  <svg class="feature-icon" style="top:628px" viewBox="0 0 48 52" aria-hidden="true">
    <polygon points="24,2 45,14 45,38 24,50 3,38 3,14" fill="#fff" stroke="#14b4ee" stroke-width="3"/>
    <rect x="16" y="14" width="12" height="7" rx="1" transform="rotate(40 22 17)" fill="none" stroke="#0a2f66" stroke-width="1.6"/>
    <line x1="24" y1="22" x2="33" y2="33" stroke="#0a2f66" stroke-width="1.8"/>
    <rect x="13" y="33" width="14" height="4" fill="none" stroke="#0a2f66" stroke-width="1.4"/>
  </svg>
  <p class="feature" style="top:638px">Our team consists of several law enforcement and operational leaders</p>

  <p class="site-url">www.<strong>vantrellrostergroup</strong>.com</p>
</section>

<!-- Banner 2: Operations -->
<section class="banner banner--ops">
  <svg class="banner__art" viewBox="0 0 500 1180" preserveAspectRatio="none" aria-hidden="true">
    <defs>
      <linearGradient id="opsBg" x1="0" y1="0" x2="0" y2="1">
        <stop offset="0" stop-color="#03163a"/>
        <stop offset="0.45" stop-color="#0a2f66"/>
        <stop offset="1" stop-color="#0d4a8f"/>
      </linearGradient>
      <linearGradient id="opsPhoto" x1="0" y1="0" x2="1" y2="1">
        <stop offset="0" stop-color="#1d3f73"/>
        <stop offset="0.5" stop-color="#0f2a55"/>
        <stop offset="1" stop-color="#08193a"/>
      </linearGradient>
      <linearGradient id="opsBase" x1="0" y1="0" x2="1" y2="1">
        <stop offset="0" stop-color="#14b4ee"/>
        <stop offset="1" stop-color="#0b5fae"/>
      </linearGradient>
    </defs>
    <rect width="500" height="1180" fill="url(#opsBg)"/>
    <polygon points="0,168 165,222 0,268" fill="#29c4f5"/>
    <polygon points="500,478 500,580 330,530" fill="#14b4ee"/>
    <polygon points="0,1020 500,1060 500,1180 0,1180" fill="url(#opsBase)"/>
    <polygon points="270,1035 500,1060 500,1110" fill="#0a2f66"/>
  </svg>
  <svg class="banner__art" viewBox="0 0 500 1180" preserveAspectRatio="none" role="img" aria-label="Photo: two officers in dark tactical uniforms at night, one speaking into a radio">
    <polygon points="0,268 165,222 500,168 500,478 330,530 0,580" fill="url(#opsPhoto)"/>
  </svg>

  <div class="brand">
    <span class="brand__line">Vantrell Roster</span>
    <span class="brand__line brand__line--sub">Group</span>
  </div>

  <svg class="feature-icon" style="top:409px" viewBox="0 0 48 52" aria-hidden="true">
    <polygon points="24,2 45,14 45,38 24,50 3,38 3,14" fill="#fff" stroke="#14b4ee" stroke-width="3"/>
    <rect x="15" y="13" width="18" height="26" rx="1.5" fill="none" stroke="#0a2f66" stroke-width="1.6"/>
    <circle cx="24" cy="20" r="3" fill="none" stroke="#0a2f66" stroke-width="1.4"/>
    <line x1="18" y1="28" x2="30" y2="28" stroke="#0a2f66" stroke-width="1.4"/>
    <line x1="18" y1="33" x2="30" y2="33" stroke="#0a2f66" stroke-width="1.4"/>
  </svg>
  <p class="feature" style="top:412px">Ability to handle nearly any detail assignment process including combinations of multiple methods</p>
  <div class="divider" style="top:476px"></div>

  <svg class="feature-icon" style="top:487px" viewBox="0 0 48 52" aria-hidden="true">
    <polygon points="24,2 45,14 45,38 24,50 3,38 3,14" fill="#fff" stroke="#14b4ee" stroke-width="3"/>
    <path d="M14 28 v-4 a10 10 0 0 1 20 0 v4" fill="none" stroke="#0a2f66" stroke-width="1.6"/>
    <rect x="12" y="25" width="4" height="8" rx="1" fill="none" stroke="#0a2f66" stroke-width="1.4"/>
    <rect x="32" y="25" width="4" height="8" rx="1" fill="none" stroke="#0a2f66" stroke-width="1.4"/>
    <text x="24" y="31" text-anchor="middle" font-family="Montserrat, sans-serif" font-size="7" fill="#0a2f66">24</text>
  </svg>
  <p class="feature" style="top:496px">Account Team approach with 24/7/365 insourced coverage of phone calls</p>
  <div class="divider" style="top:550px"></div>

  <svg class="feature-icon" style="top:561px" viewBox="0 0 48 52" aria-hidden="true">
    <polygon points="24,2 45,14 45,38 24,50 3,38 3,14" fill="#fff" stroke="#14b4ee" stroke-width="3"/>
    <circle cx="24" cy="16" r="3" fill="none" stroke="#0a2f66" stroke-width="1.4"/>
    <path d="M24 21 v5 M15 31 v-5 h18 v5" fill="none" stroke="#0a2f66" stroke-width="1.4"/>
    <circle cx="15" cy="33" r="2.5" fill="none" stroke="#0a2f66" stroke-width="1.4"/>
    <circle cx="24" cy="33" r="2.5" fill="none" stroke="#0a2f66" stroke-width="1.4"/>
    <circle cx="33" cy="33" r="2.5" fill="none" stroke="#0a2f66" stroke-width="1.4"/>
  </svg>
  <p class="feature" style="top:570px">Multiple operations centers with complete failover and disaster recovery</p>
  <div class="divider" style="top:620px"></div>

  <svg class="feature-icon" style="top:628px" viewBox="0 0 48 52" aria-hidden="true">
    <polygon points="24,2 45,14 45,38 24,50 3,38 3,14" fill="#fff" stroke="#14b4ee" stroke-width="3"/>
    <rect x="14" y="13" width="16" height="24" rx="1.5" fill="none" stroke="#0a2f66" stroke-width="1.6"/>
    <line x1="18" y1="20" x2="26" y2="20" stroke="#0a2f66" stroke-width="1.4"/>
    <line x1="18" y1="25" x2="26" y2="25" stroke="#0a2f66" stroke-width="1.4"/>
    <path d="M30 26 l5 2 v4 q0 4 -5 6 q-5 -2 -5 -6 v-4 z" fill="#fff" stroke="#0a2f66" stroke-width="1.4"/>
    <path d="M28 32 l2 2 l3 -3" fill="none" stroke="#0a2f66" stroke-width="1.3"/>
  </svg>
  <p class="feature" style="top:638px">Industry-leading, flexible liability and worker's comp insurance which is primary to yours</p>

  <p class="site-url">www.<strong>vantrellrostergroup</strong>.com</p>
</section>

</body>
</html>
```